Transform Your Giving

I need a tri-fold brochure that will fit in a standard number 10 business envelope. Meadowlark and Allied Services is a charitable nonprofit. The goal of this brochure is to stimulate people into thinking about other ways to make a donation. The design should communicate the essential information on donation options, create a sense of professional integrity, be graphically sharp, easy to read and laid out in a way that doesn't make the material appear crowded.

```html
<!DOCTYPE html>
<html lang="en">
<head>
<meta charset="utf-8">
<title>Transform Your Giving – Tri-fold Brochure</title>
<link href="https://fonts.googleapis.com/css2?family=Bebas+Neue&family=Montserrat:ital,wght@0,400;0,600;0,700;0,800;1,600;1,700&display=swap" rel="stylesheet">
<style>
:root{
  --purple:#2c2878;
  --purple-mid:#3a3394;
  --purple-light:#4a43a8;
  --green:#4cb848;
  --green-dark:#3fa53b;
  --ink:#222236;
  --white:#ffffff;
  --page:#ebebeb;
}
*{box-sizing:border-box;margin:0;padding:0}
html,body{width:720px;height:1200px;overflow:hidden}
body{background:var(--page);font-family:"Montserrat",sans-serif;color:var(--ink);position:relative}
.spread{position:absolute;left:49px;width:1282px;height:991px;transform:scale(.4852);transform-origin:0 0;background:var(--white);box-shadow:0 4px 14px rgba(0,0,0,.18);overflow:hidden}
.spread--outside{top:66px}
.spread--inside{top:616px}
.panel{position:absolute;top:0;height:991px;overflow:hidden}
.panel--purple{background:linear-gradient(160deg,var(--purple) 0%,var(--purple-mid) 55%,var(--purple) 100%);color:var(--white)}
.abs{position:absolute}
.body-text{font-size:13px;line-height:15.6px}
.center{text-align:center}
.photo{position:absolute}
.banner-title{font-family:"Bebas Neue",sans-serif;color:var(--white);background:var(--purple);font-size:34px;line-height:42px;padding:0 20px 0 30px;border-radius:0 22px 22px 0}
.checklist{list-style:none;font-size:13px;font-weight:600}
.checklist li{display:flex;align-items:center;gap:8px;height:27.5px}
.tick{width:10px;height:10px;flex:none}
.pill-how{background:var(--green);color:var(--white);font-weight:700;font-size:15px;letter-spacing:.5px;line-height:26px;padding:0 9px;border-radius:0 8px 8px 0;display:inline-block}
.opt-title{color:var(--green);font-weight:700;font-size:16px;line-height:19px}
.opt-tag{color:var(--green);font-weight:700;font-style:italic;font-size:12.5px;line-height:15.5px}
.brand-name{font-family:"Montserrat",sans-serif;font-weight:800;text-align:center}
.contact-ico{width:18px;height:18px;border-radius:50%;background:var(--green);margin:0 auto 4px}
.bubble{position:absolute;width:100px;height:100px;border-radius:50%;background:rgba(255,255,255,.72);box-shadow:0 0 0 2px rgba(255,255,255,.9) inset,0 4px 10px rgba(0,0,0,.15);display:flex;flex-direction:column;align-items:center;justify-content:center;font-size:12px;color:var(--purple);font-weight:600;text-align:center;line-height:13px}
.bubble svg{margin-bottom:4px}
.quote-mark{font-family:"Montserrat",sans-serif;font-weight:800;font-size:96px;fill:var(--green)}
.site-pill{position:absolute;height:28px;border-radius:14px 0 0 14px;background:var(--purple);color:var(--white);font-size:15px;line-height:28px;padding-left:12px;white-space:nowrap}
</style>
</head>
<body>

<!-- ============ OUTSIDE SPREAD ============ -->
<section class="spread spread--outside">

  <!-- Back panel: impact -->
  <div class="panel" style="left:0;width:425px;background:var(--white)">
    <div class="photo" role="img" aria-label="Photo of a young woman comforting an older woman on a sofa" style="left:0;top:0;width:425px;height:640px;background:linear-gradient(170deg,#cfc7bd 0%,#b7aea3 45%,#8f8f95 100%)"></div>
    <svg class="abs" style="left:0;top:540px" width="425" height="160" viewBox="0 0 425 160" aria-hidden="true">
      <path d="M0 160 L0 70 Q170 -10 425 100 L425 160 Z" fill="var(--white)"/>
      <path d="M0 70 Q170 -10 425 100 L425 60 Q200 -40 0 62 Z" fill="var(--green)"/>
    </svg>
    <div class="abs banner-title" style="left:0;top:658px">THE IMPACT OF YOUR GIFT</div>
    <p class="abs body-text" style="left:30px;top:727px;width:370px">Your generosity drives our mission. With every Smart gift you're supporting Meadowlark and Allied Services. Join our community of Smart Givers today and make an enduring impact. With Smart Giving your generosity reaches further. Begin your Smart Giving journey with us today.</p>
    <ul class="abs checklist" style="left:30px;top:832px">
      <li><svg class="tick" viewBox="0 0 10 10"><rect x=".5" y=".5" width="9" height="9" fill="none" stroke="var(--purple)"/><path d="M2 5l2 2 4-5" fill="none" stroke="var(--purple)" stroke-width="1.3"/></svg>Stocks and Securities</li>
      <li><svg class="tick" viewBox="0 0 10 10"><rect x=".5" y=".5" width="9" height="9" fill="none" stroke="var(--purple)"/><path d="M2 5l2 2 4-5" fill="none" stroke="var(--purple)" stroke-width="1.3"/></svg>DAFs</li>
      <li><svg class="tick" viewBox="0 0 10 10"><rect x=".5" y=".5" width="9" height="9" fill="none" stroke="var(--purple)"/><path d="M2 5l2 2 4-5" fill="none" stroke="var(--purple)" stroke-width="1.3"/></svg>QCDs</li>
      <li><svg class="tick" viewBox="0 0 10 10"><rect x=".5" y=".5" width="9" height="9" fill="none" stroke="var(--purple)"/><path d="M2 5l2 2 4-5" fill="none" stroke="var(--purple)" stroke-width="1.3"/></svg>Crypto</li>
      <li><svg class="tick" viewBox="0 0 10 10"><rect x=".5" y=".5" width="9" height="9" fill="none" stroke="var(--purple)"/><path d="M2 5l2 2 4-5" fill="none" stroke="var(--purple)" stroke-width="1.3"/></svg>Charitable Annuity</li>
    </ul>
  </div>

  <!-- Middle panel: contact -->
  <div class="panel panel--purple" style="left:425px;width:430px">
    <p class="abs body-text center" style="left:30px;top:30px;width:370px">To learn more about Smart Giving Options and how they can benefit you and Meadowlark and Allied Services, please reach out to our team. We're here to help you navigate these giving methods and answer any question you may have.</p>
    <svg class="abs" style="left:40px;top:135px" width="355" height="130" viewBox="0 0 355 130" aria-hidden="true">
      <text class="quote-mark" x="0" y="100">“</text>
      <path d="M65 25 H330 Q350 25 350 45 V82 Q350 102 330 102 H220" fill="none" stroke="var(--green)" stroke-width="1.5"/>
      <text class="quote-mark" x="155" y="178">”</text>
    </svg>
    <p class="abs" style="left:43px;top:184px;width:330px;font-size:17px;line-height:20px;font-style:italic">Being kind to others is a way of being good to yourself.<br><b style="font-weight:700">- Ruth Ellery</b></p>
    <div class="abs" style="left:60px;top:300px;width:310px">
      <div style="width:14px;height:14px;border-radius:50%;background:var(--white);margin:0 auto 8px"></div>
      <p class="brand-name" style="font-size:20px;line-height:24px;color:var(--white)">MEADOWLARK AND<br>ALLIED SERVICES</p>
    </div>
    <div class="abs center" style="left:58px;top:412px;width:316px;height:60px;border-radius:16px;background:var(--green);font-size:13px;line-height:15.5px;padding-top:6px;box-shadow:0 0 18px rgba(255,255,255,.35)">If you do not have a will, go to<br><b>www.WillReady.org</b><br>In 20 minutes you can have a legal will for free.</div>
    <div class="abs center" style="left:0;top:527px;width:430px">
      <p style="font-size:16px;font-weight:700;text-decoration:underline;letter-spacing:.5px">CONTACT US</p>
      <p class="body-text" style="margin-top:16px">Have more question?<br>Please contact us at Meadowlark &amp; Allied Services</p>
      <div class="contact-ico" style="margin-top:10px"></div>
      <p class="body-text">1420 Prairie View Rd.<br>Suite 2, Fargo, ND&nbsp; 58102</p>
      <div class="contact-ico" style="margin-top:10px"></div>
      <p class="body-text">555-014-2200 (ext. 100)</p>
      <div class="contact-ico" style="margin-top:12px"></div>
      <p class="body-text">mhollis@meadowlarkallied.org</p>
      <div class="contact-ico" style="margin-top:12px"></div>
      <p class="body-text">www.meadowlarkallied.org</p>
      <p style="font-size:16px;font-weight:700;text-decoration:underline;margin-top:40px">Follow us:</p>
      <svg style="margin-top:6px" width="130" height="24" viewBox="0 0 130 24" aria-hidden="true">
        <line x1="12" y1="12" x2="118" y2="12" stroke="var(--green)" stroke-width="1.5"/>
        <circle cx="12" cy="12" r="10" fill="var(--green)"/>
        <circle cx="65" cy="12" r="10" fill="var(--green)"/>
        <circle cx="118" cy="12" r="10" fill="var(--green)"/>
      </svg>
    </div>
    <p class="abs center" style="left:40px;top:922px;width:350px;font-size:8px;line-height:9.5px">This material has been prepared for informational purposes only and is not intended to provide tax, accounting, or legal advice. Meadowlark and Allied Services is not a professional fiduciary organization. Please consult with your tax advisor or financial professional before making a decision about Smart Giving.</p>
  </div>

  <!-- Front cover -->
  <div class="panel" style="left:855px;width:427px;background:var(--white)">
    <h1 class="abs center" style="left:0;top:26px;width:427px;font-family:'Bebas Neue',sans-serif;font-weight:400;font-size:52px;line-height:50px;color:var(--green)">TRANSFORM YOUR GIVING</h1>
    <div class="abs center" style="left:45px;top:76px;width:340px;height:30px;border-radius:15px;background:var(--purple);color:var(--white);font-weight:800;font-size:23px;line-height:30px;letter-spacing:.5px">BE STRATEGIC, BE SMART</div>
    <p class="abs center" style="left:0;top:114px;width:427px;font-size:17px;line-height:21px">Discover the impact of Smart Giving with<br>Meadowlark and Allied Services</p>
    <div class="photo" role="img" aria-label="Photo of a woman with glasses using a smartphone at an outdoor cafe table" style="left:0;top:170px;width:427px;height:720px;background:linear-gradient(180deg,#c7c48f 0%,#a9a57a 30%,#8b8375 60%,#c9c6c2 100%)"></div>
    <svg class="abs" style="left:0;top:165px" width="427" height="95" viewBox="0 0 427 95" aria-hidden="true">
      <path d="M0 0 H427 V20 Q280 100 0 10 Z" fill="var(--white)"/>
      <path d="M30 18 Q260 95 427 15 V35 Q260 110 30 18 Z" fill="var(--green)"/>
    </svg>
    <div class="bubble" style="left:30px;top:228px">
      <svg width="54" height="46" viewBox="0 0 54 46"><g fill="none" stroke="var(--purple)" stroke-width="2.5"><circle cx="14" cy="14" r="11"/><circle cx="40" cy="14" r="11"/><circle cx="27" cy="33" r="11"/></g></svg>Crypto</div>
    <div class="bubble" style="left:294px;top:322px">
      <svg width="50" height="46" viewBox="0 0 50 46"><g fill="none" stroke="var(--purple)" stroke-width="2.5"><circle cx="18" cy="17" r="13"/><circle cx="18" cy="17" r="6"/><circle cx="34" cy="31" r="12"/><circle cx="34" cy="31" r="5"/></g></svg>DAF's</div>
    <div class="bubble" style="left:30px;top:490px">
      <svg width="54" height="40" viewBox="0 0 54 40"><g fill="var(--purple)"><rect x="8" y="22" width="6" height="15"/><rect x="18" y="14" width="6" height="23"/><rect x="28" y="18" width="6" height="19"/><rect x="38" y="8" width="6" height="29"/></g><path d="M2 2 V38 H52" fill="none" stroke="var(--purple)" stroke-width="3"/></svg>Stocks &amp;<br>Securities</div>
    <div class="bubble" style="left:294px;top:558px">
      <svg width="48" height="48" viewBox="0 0 48 48"><g fill="var(--purple)"><rect x="4" y="16" width="40" height="9"/><rect x="7" y="27" width="15" height="19"/><rect x="26" y="27" width="15" height="19"/></g><path d="M24 15 Q14 0 10 10 Q10 15 24 15 Q34 0 38 10 Q38 15 24 15" fill="none" stroke="var(--purple)" stroke-width="3"/></svg>QCDs</div>
    <div class="bubble" style="left:30px;top:695px">
      <svg width="54" height="44" viewBox="0 0 54 44"><g fill="none" stroke="var(--purple)" stroke-width="2.5"><ellipse cx="14" cy="38" rx="10" ry="3.5"/><ellipse cx="14" cy="32" rx="10" ry="3.5"/><ellipse cx="34" cy="38" rx="10" ry="3.5"/><ellipse cx="34" cy="32" rx="10" ry="3.5"/><ellipse cx="34" cy="26" rx="10" ry="3.5"/></g><circle cx="42" cy="8" r="6" fill="var(--purple)"/></svg>Charitable<br>Annuity</div>
    <svg class="abs" style="left:0;top:820px" width="427" height="171" viewBox="0 0 427 171" aria-hidden="true">
      <path d="M0 60 Q180 -20 427 60 V171 H0 Z" fill="var(--purple)"/>
      <path d="M0 80 Q200 10 427 78 V171 H0 Z" fill="var(--white)"/>
    </svg>
    <div class="abs" style="left:50px;top:870px;width:327px">
      <div style="width:18px;height:18px;border-radius:50%;background:var(--green);margin:0 auto 10px"></div>
      <p class="brand-name" style="font-size:24px;line-height:28px;color:var(--purple)">MEADOWLARK AND<br>ALLIED SERVICES</p>
    </div>
  </div>
</section>

<!-- ============ INSIDE SPREAD ============ -->
<section class="spread spread--inside">

  <!-- Inside left: stocks & DAF -->
  <div class="panel panel--purple" style="left:0;width:428px">
    <p class="abs body-text" style="left:30px;top:28px;width:370px">We would like to introduce you to five Strategic and Smart ways to give that could potentially be more beneficial to you compared to traditional cash donations. We encourage you to keep this information as a guide for your future contributions.</p>
    <svg class="abs" style="left:30px;top:132px" width="75" height="64" viewBox="0 0 75 64" aria-hidden="true">
      <path d="M2 2 V62 H73" fill="none" stroke="var(--green)" stroke-width="4"/>
      <g fill="var(--green)"><rect x="14" y="34" width="8" height="22"/><rect x="28" y="24" width="8" height="32"/><rect x="42" y="30" width="8" height="26"/><rect x="56" y="18" width="8" height="38"/></g>
      <path d="M12 24 L28 12 L42 20 L66 4" fill="none" stroke="var(--green)" stroke-width="3"/>
    </svg>
    <div class="abs" style="left:118px;top:130px;width:280px">
      <p class="opt-title">Gifts of Stocks or Appreciated Assets Strategic &amp; Smart</p>
      <p class="opt-tag">Consider your long-term publicly traded stock as a way to give to your favorite charity.</p>
    </div>
    <p class="abs body-text" style="left:30px;top:228px;width:375px">You can make a significantly bigger impact when you donate long-term appreciated securities, including stock, mutual funds, and bonds, directly to your favorite charity.</p>
    <div class="abs pill-how" style="left:28px;top:292px">HOW DOES IT WORK?</div>
    <p class="abs body-text" style="left:27px;top:343px;width:375px">When you donate stock to a charity, you will generally take a tax deduction for the full market value. Because you are donating stock, your contribution and tax deduction may be significantly higher than contributing the after-tax proceeds. The same benefits apply when you donate mutual funds or bonds.</p>
    <svg class="abs" style="left:30px;top:485px" width="76" height="76" viewBox="0 0 76 76" aria-hidden="true">
      <g fill="none" stroke="var(--green)" stroke-width="3"><circle cx="27" cy="27" r="21"/><circle cx="27" cy="27" r="11"/><circle cx="50" cy="50" r="20"/><circle cx="50" cy="50" r="10"/></g>
    </svg>
    <div class="abs" style="left:118px;top:484px;width:280px">
      <p class="opt-title">Donor-Advised Fund (DAF)<br>Strategic &amp; Smart</p>
      <p class="opt-tag">Consider a DAF – a simple, flexible, and tax-advantageous way to give to your favorite charities.</p>
    </div>
    <p class="abs body-text" style="left:30px;top:583px;width:370px">A Donor-Advised Fund (DAF), is like a charitable investment account for the sole purpose of supporting your favorite charities.</p>
    <div class="abs pill-how" style="left:28px;top:647px">HOW DOES IT WORK?</div>
    <p class="abs body-text" style="left:27px;top:698px;width:375px">You establish a DAF and contribute cash, stocks, or non-publicly traded assets, cryptocurrency, and private company stock to be eligible for an immediate tax deduction. Those funds are contributed for tax-free growth. You can recommend grants be made from your DAF to any IRS qualified public charity.</p>
    <div class="photo" role="img" aria-label="Photo of a woman with glasses working on a laptop at home" style="left:0;top:830px;width:428px;height:161px;background:linear-gradient(90deg,#e6ece4 0%,#d9d4cc 50%,#eef0ec 100%)"></div>
    <svg class="abs" style="left:0;top:800px" width="428" height="191" viewBox="0 0 428 191" aria-hidden="true">
      <path d="M0 0 H428 V191 Q260 20 0 42 Z" fill="var(--purple)"/>
      <path d="M0 28 Q260 0 428 191 L416 191 Q250 20 0 44 Z" fill="var(--green)"/>
    </svg>
  </div>

  <!-- Inside middle: QCD -->
  <div class="panel" style="left:431px;width:423px;background:var(--white)">
    <div class="photo" role="img" aria-label="Photo of a smiling woman in a yellow cardigan holding a phone beside a laptop" style="left:0;top:0;width:423px;height:510px;background:linear-gradient(180deg,#eceae6 0%,#e5cfa9 45%,#dcb55a 75%,#ffffff 100%)"></div>
    <svg class="abs" style="left:24px;top:548px" width="66" height="76" viewBox="0 0 66 76" aria-hidden="true">
      <g fill="var(--green)"><rect x="2" y="24" width="62" height="14"/><rect x="6" y="42" width="24" height="32"/><rect x="36" y="42" width="24" height="32"/></g>
      <path d="M33 22 Q18 0 12 12 Q10 22 33 22 Q48 0 54 12 Q56 22 33 22" fill="none" stroke="var(--green)" stroke-width="4"/>
    </svg>
    <div class="abs" style="left:103px;top:543px;width:300px">
      <p class="opt-title">Qualified Charitable Distributions (QCDs) Strategic &amp; Smart</p>
      <p class="opt-tag">Consider a QCD – when planning your IRA withdrawal strategy...and donate to your favorite charity.</p>
    </div>
    <p class="abs body-text" style="left:25px;top:653px;width:370px">IRA owners at age 70 or over can transfer dollars from their IRA to charity tax-free each year. These transfers known as Qualified Charitable Distributions (QCDs) offer eligible older Americans a great way to easily give to charity.</p>
    <div class="abs pill-how" style="left:23px;top:763px">HOW DOES IT WORK?</div>
    <p class="abs body-text" style="left:25px;top:810px;width:370px">Are you 72 and required to take a minimum distribution (RMD) from your IRA but do not need the funds? Consider a Qualified Charitable Distribution. Normally, distributions from a traditional IRA are taxable when received. With a QCD, these distributions become tax-free when paid directly from the IRA to your favorite eligible charity. An IRA owner wishing to make a QCD should contact their IRA trustee, allowing time to complete the transaction before the end of the year to receive the tax benefit.</p>
  </div>

  <!-- Inside right: crypto & annuity -->
  <div class="panel panel--purple" style="left:855px;width:427px">
    <svg class="abs" style="left:32px;top:28px" width="66" height="58" viewBox="0 0 66 58" aria-hidden="true">
      <g fill="none" stroke="var(--green)" stroke-width="3"><circle cx="17" cy="17" r="14"/><circle cx="48" cy="17" r="14"/><circle cx="32" cy="40" r="14"/></g>
    </svg>
    <div class="abs" style="left:108px;top:27px;width:300px">
      <p class="opt-title">Cryptocurrency Strategic &amp; Smart</p>
      <p class="opt-tag">Consider donating Bitcoin and other cryptocurrencies to your favorite charity.</p>
    </div>
    <p class="abs body-text" style="left:30px;top:107px;width:370px">Bitcoin and other cryptocurrencies can be donated to charity just like other appreciated assets such as stocks and other business interests. Before you sell bitcoin and donate the after-tax proceeds, consider donating your bitcoin directly to a favorite charity.</p>
    <div class="abs pill-how" style="left:30px;top:205px">HOW DOES IT WORK?</div>
    <p class="abs body-text" style="left:30px;top:248px;width:370px">Many donors find it useful to open a Donor-Advised Fund (DAF). This strategy includes two significant benefits, both for you and your favorite charity.</p>
    <div class="abs" style="left:30px;top:316px;width:370px">
      <div style="display:flex;gap:12px"><svg class="tick" style="width:13px;height:13px;margin-top:2px" viewBox="0 0 10 10"><rect x=".5" y=".5" width="9" height="9" fill="none" stroke="var(--white)"/><path d="M2 5l2 2 4-5" fill="none" stroke="var(--white)" stroke-width="1.3"/></svg><p class="body-text">Your tax deduction will be equal to the fair market value of the donated bitcoin (as determined by a qualified appraisal).</p></div>
      <div style="display:flex;gap:12px;margin-top:17px"><svg class="tick" style="width:13px;height:13px;margin-top:2px" viewBox="0 0 10 10"><rect x=".5" y=".5" width="9" height="9" fill="none" stroke="var(--white)"/><path d="M2 5l2 2 4-5" fill="none" stroke="var(--white)" stroke-width="1.3"/></svg><p class="body-text">Your cryptocurrency donation is tax-smart because it may eliminate capital gains taxes on the value /appreciation AND your favorite charity will receive 100% of the value of the contribution.</p></div>
    </div>
    <p class="abs body-text" style="left:30px;top:460px;width:375px">Often charities are not able to accept direct donations of bitcoin/crypto so using a DAF is a great way to donate these assets.</p>
    <svg class="abs" style="left:30px;top:540px" width="66" height="64" viewBox="0 0 66 64" aria-hidden="true">
      <g fill="none" stroke="var(--green)" stroke-width="3"><ellipse cx="14" cy="58" rx="11" ry="4"/><ellipse cx="14" cy="50" rx="11" ry="4"/><ellipse cx="38" cy="58" rx="11" ry="4"/><ellipse cx="38" cy="50" rx="11" ry="4"/><ellipse cx="38" cy="42" rx="11" ry="4"/><path d="M2 10 H20 M2 18 H14"/></g>
      <circle cx="52" cy="12" r="9" fill="var(--green)"/>
    </svg>
    <div class="abs" style="left:108px;top:536px;width:300px">
      <p class="opt-title">Charitable Gift Annuity<br>Strategic &amp; Smart</p>
      <p class="opt-tag">Consider establishing a Charitable<br>Gift Annuity</p>
    </div>
    <p class="abs body-text" style="left:30px;top:625px;width:370px">You make a donation to a single charity. The gift is set aside in a reserve account and invested.</p>
    <div class="abs pill-how" style="left:30px;top:670px">HOW DOES IT WORK?</div>
    <p class="abs body-text" style="left:30px;top:715px;width:375px">A charitable gift annuity is a contract between a donor and a charity. As a donor, you make a sizable gift to charity using cash, securities, or possibly other assets. This money is then invested. In return, you become eligible to take a partial tax deduction for your donation, plus you receive a fixed stream of income from the charity for the rest of your life. At the end of your life (as well as your spouse's, if you're giving as a couple), the charity receives the remainder of the gift.</p>
    <svg class="abs" style="left:0;top:880px" width="427" height="111" viewBox="0 0 427 111" aria-hidden="true">
      <path d="M40 111 Q200 20 427 18 V0 Q200 5 40 111 Z" fill="var(--green)"/>
      <path d="M55 111 Q210 30 427 28 V111 Z" fill="var(--white)"/>
    </svg>
    <div class="site-pill" style="left:172px;top:933px;width:255px">www.meadowlarkallied.org</div>
  </div>
</section>

</body>
</html>
```